Every Shelf Set Neatly or ESN Organized needs a business card design. ESN Organized is a professi

We need a business card design that is clean, sharp and conveys a sense of organization. I already have a logo.

Target Market(s)

Families (specifically mothers), small business owners, parents, seniors

Industry/Entity Type

Business

Contact Information for Business Card

My website is www.esnorganized-example.com and my sociallink page is http://www.sociallink-example.com/everyshelfsetneatly. The phone number is 418-552-7094 and I want to be listed as Lorna M. Pelham, Owner

Requirements
Must have
• My logo.

```html
<!DOCTYPE html>
<html lang="en">
<head>
<meta charset="utf-8">
<title>ESN Organized – Business Card</title>
<link href="https://fonts.googleapis.com/css2?family=Open+Sans:ital,wght@0,400;0,600;0,700;1,400&family=Montserrat:wght@400&display=swap" rel="stylesheet">
<style>
  :root {
    --card-blue: #0b7ad9;
    --ink-white: #ffffff;
    --divider: rgba(255,255,255,0.55);
    --backdrop: #e9e9eb;
  }
  html, body {
    margin: 0;
    width: 1200px;
    height: 900px;
    overflow: hidden;
    background: var(--backdrop);
  }
  .canvas {
    position: relative;
    width: 1200px;
    height: 900px;
  }
  .card {
    position: absolute;
    left: 143px;
    top: 168px;
    width: 913px;
    height: 563px;
    background: var(--card-blue);
    border-radius: 6px 130px 6px 6px;
    color: var(--ink-white);
    font-family: "Open Sans", Arial, sans-serif;
    box-shadow: 0 10px 30px rgba(0,0,0,0.15);
  }
  .brand {
    position: absolute;
    left: 50px;
    top: 62px;
    display: flex;
    align-items: center;
    gap: 16px;
  }
  .brand-mark {
    width: 18px;
    height: 18px;
    border-radius: 50%;
    background: var(--ink-white);
  }
  .brand-name {
    font-family: "Montserrat", "Open Sans", sans-serif;
    font-weight: 400;
    font-size: 38px;
    letter-spacing: 5px;
    color: var(--ink-white);
  }
  .holder {
    position: absolute;
    left: 50px;
    top: 200px;
  }
  .holder-name {
    font-size: 33px;
    font-weight: 700;
    margin: 0;
    line-height: 1.1;
  }
  .holder-role {
    font-size: 22px;
    margin: 4px 0 0;
  }
  .contacts {
    position: absolute;
    left: 50px;
    top: 298px;
    margin: 0;
    padding: 0;
    list-style: none;
    font-size: 23px;
  }
  .contacts li {
    display: flex;
    align-items: center;
    gap: 12px;
    height: 38.5px;
  }
  .contacts svg {
    width: 18px;
    height: 18px;
    flex: none;
    fill: var(--ink-white);
  }
  .tagline {
    position: absolute;
    left: 50px;
    top: 476px;
    margin: 0;
    font-family: Arial, "Open Sans", sans-serif;
    font-style: italic;
    font-size: 23px;
  }
</style>
</head>
<body>
<div class="canvas">
  <section class="card" aria-label="ESN Organized business card">
    <div class="brand">
      <span class="brand-mark"></span>
      <span class="brand-name">ESN Organized</span>
    </div>

    <div class="holder">
      <h1 class="holder-name">Lorna M. Pelham</h1>
      <p class="holder-role">Owner</p>
    </div>

    <ul class="contacts">
      <li>
        <svg viewBox="0 0 24 24" aria-hidden="true"><path d="M6.6 10.8a15.1 15.1 0 0 0 6.6 6.6l2.2-2.2c.3-.3.7-.4 1-.2 1.1.4 2.3.6 3.6.6.6 0 1 .4 1 1V20c0 .6-.4 1-1 1C10.6 21 3 13.4 3 4c0-.6.4-1 1-1h3.5c.6 0 1 .4 1 1 0 1.3.2 2.5.6 3.6.1.3 0 .7-.2 1z"/></svg>
        418-552-7094
      </li>
      <li>
        <svg viewBox="0 0 24 24" aria-hidden="true"><path d="M2 5h20v14H2z M2 5l10 8 10-8" fill="none" stroke="#fff" stroke-width="0"/><path d="M2 5h20v2l-10 7L2 7z"/><path d="M2 9l10 7 10-7v10H2z"/></svg>
        info@esnorganized-example.com
      </li>
      <li>
        <svg viewBox="0 0 24 24" aria-hidden="true"><circle cx="12" cy="12" r="10" fill="none" stroke="#fff" stroke-width="2"/><path d="M2 12h20M12 2c3 3 3 17 0 20M12 2c-3 3-3 17 0 20" fill="none" stroke="#fff" stroke-width="1.6"/></svg>
        www.esnorganized-example.com
      </li>
      <li>
        <svg viewBox="0 0 24 24" aria-hidden="true"><rect x="3" y="3" width="18" height="18" rx="3"/></svg>
        sociallink/everyshelfsetneatly
      </li>
    </ul>

    <p class="tagline">We keep you organized in all ways, and always organized</p>
  </section>
</div>
</body>
</html>
```